BrivoTerna. Lantern of the Steady Harvest. Business card

Professional business card for BrivoTerna (Lantern of the Steady Harvest)
My rationale: Strategy-> Execution-> Results-> Value that lead to the BrivoTerna name: We put the Lantern of the Steady Harvest.
We deliver value to our customers helping them at defining a good strategy (cyan arrow). 90% of well formulated strategies fail due to poor execution so we also consider strategical execution very important (green arrow). Due to the execution we obtain the results (blue arrow). Finally, the results provide feedback to redefine strategy, and the new strategy has to be executed and new results obtained providing new feedback and on and on. It's like a wheel that finally, must create corporate value: value for shareholders, staholders, employees, providers...-

Target Market(s)

CEOs and steering comitees , invewrnent funds

Industry/Entity Type

Business Consultant

Contact Information for Business Card

Teodoro Vinsquel
CEO & Founder
teodoro.vinsquel@brivoterna-example.com
Mobile: +34 655.803.912
www.brivoterna-example.com

Colors

Designer to choose colors to be used in the design.

Requirements
Nice to have
• Nice to hace the words: Strategy, execution, results
• Nice to vave the claim: Lantern of the Steady Harvest
• The three colors should be shown:
• cyan for STRATEGY
• green for EXECUTION
• blue for RESULTS
Should not have
• Complete black background

```html
<!DOCTYPE html>
<html lang="en">
<head>
<meta charset="utf-8">
<title>BrivoTerna – Business Card</title>
<link rel="stylesheet" href="https://fonts.googleapis.com/css2?family=Montserrat:wght@300;400&family=Open+Sans:wght@700&family=Oswald:wght@600&display=swap">
<style>
  :root {
    --page-bg: #151515;
    --card-top: #262626;
    --card-bottom: #1b1b1b;
    --accent-green: #a6c85a;
    --accent-cyan: #1aa6e4;
    --text-white: #f4f4f4;
  }
  * { margin: 0; padding: 0; box-sizing: border-box; }
  html, body {
    width: 1200px;
    height: 900px;
    overflow: hidden;
    background: var(--page-bg);
  }
  .canvas {
    width: 1200px;
    height: 900px;
    display: flex;
    flex-direction: column;
    align-items: center;
    justify-content: center;
    gap: 30px;
  }
  .card {
    position: relative;
    width: 720px;
    height: 410px;
    background: linear-gradient(160deg, var(--card-top), var(--card-bottom));
    border-bottom: 5px solid var(--accent-green);
    box-shadow: 0 12px 30px rgba(0, 0, 0, 0.55);
  }
  .card-front {
    display: flex;
    align-items: center;
    justify-content: center;
  }
  .brand-name {
    font-family: "Open Sans", sans-serif;
    font-weight: 700;
    font-size: 72px;
    letter-spacing: -1px;
    color: var(--text-white);
  }
  .card-back {
    display: flex;
    align-items: center;
    padding-left: 60px;
  }
  .identity {
    text-align: right;
    width: 240px;
  }
  .person-name {
    font-family: "Oswald", sans-serif;
    font-weight: 600;
    font-size: 28px;
    line-height: 1.1;
    color: var(--accent-cyan);
    text-transform: uppercase;
    letter-spacing: 0.3px;
  }
  .person-role {
    font-family: "Montserrat", sans-serif;
    font-weight: 300;
    font-size: 18px;
    color: var(--text-white);
    margin-top: 2px;
  }
  .divider {
    width: 2px;
    height: 72px;
    background: var(--accent-green);
    margin: 0 18px 0 20px;
  }
  .contact-list {
    list-style: none;
    font-family: "Montserrat", sans-serif;
    font-weight: 400;
    font-size: 15px;
    color: var(--text-white);
    letter-spacing: 0.4px;
  }
  .contact-item {
    display: flex;
    align-items: center;
    gap: 9px;
    line-height: 26px;
  }
  .contact-icon {
    width: 13px;
    height: 13px;
    flex: none;
  }
  .web-domain { color: var(--accent-cyan); }
</style>
</head>
<body>
<main class="canvas">
  <section class="card card-front" aria-label="Card front">
    <span class="brand-name">BrivoTerna</span>
  </section>

  <section class="card card-back" aria-label="Card back">
    <div class="identity">
      <p class="person-name">Teodoro Vinsquel</p>
      <p class="person-role">CEO &amp; Founder</p>
    </div>
    <div class="divider"></div>
    <ul class="contact-list">
      <li class="contact-item">
        <svg class="contact-icon" viewBox="0 0 16 16" aria-hidden="true">
          <path d="M4 1.5 L6.5 1 L7.5 4.5 L5.8 5.6 C6.6 7.6 8.3 9.4 10.4 10.2 L11.5 8.5 L15 9.5 L14.5 12 C14.3 13.5 13 14.5 11.5 14.3 C6.5 13.5 2.5 9.5 1.7 4.5 C1.5 3 2.5 1.7 4 1.5 Z" fill="var(--accent-cyan)"/>
        </svg>
        <span>+34 655.803.912</span>
      </li>
      <li class="contact-item">
        <svg class="contact-icon" viewBox="0 0 16 16" aria-hidden="true">
          <rect x="1" y="3" width="14" height="10" rx="1" fill="none" stroke="var(--accent-cyan)" stroke-width="1.6"/>
          <path d="M1.5 3.5 L8 9 L14.5 3.5" fill="none" stroke="var(--accent-cyan)" stroke-width="1.6"/>
        </svg>
        <span>teodoro.vinsquel@brivoterna-example.com</span>
      </li>
      <li class="contact-item">
        <svg class="contact-icon" viewBox="0 0 16 16" aria-hidden="true">
          <circle cx="8" cy="8" r="6.5" fill="none" stroke="var(--accent-cyan)" stroke-width="1.5"/>
          <ellipse cx="8" cy="8" rx="2.8" ry="6.5" fill="none" stroke="var(--accent-cyan)" stroke-width="1.2"/>
          <path d="M1.5 8 H14.5 M2.8 4.5 H13.2 M2.8 11.5 H13.2" stroke="var(--accent-cyan)" stroke-width="1.2"/>
        </svg>
        <span>www.<span class="web-domain">brivoterna-example</span>.com</span>
      </li>
    </ul>
  </section>
</main>
</body>
</html>
```